****Business Card Design for Quarrystone Development. Design based around attached logo/company name

I’m looking for business card design for my company Quarrystone Development Group,LLC. Design should be professional, sharp and minimal. Outside of the attached logos, greyscale colors for remainder of cards. My thoughts are two-sided card with attached logo on one side and my info on the other but open to one-sided as well with right design.
Target Market(s)
Real estate professionals including banks, private investors, property owners, developers, commercial tenants like Brewlantern, Grovika or Tanquist’s.
Industry/Entity Type
Commercial real estate development and investments.
Contact Information for Business Card
Name, title, email, phone #’s, web address and physical address
Font styles to use
Other font styles liked:
- Helvetica, Garamond, etc
Colors
Designer to choose only greyscale colors for use in the design.
Requirements
Must have
- Attached logo first or second options.
Nice to have
- Two sided card with logo on one side. Attached Logo/company name can be laid out any way that flows as long as it’s legible.name
Should not have
- No loud colors. ***Please do not include logo, I have removed the company design with a logo image.

```html
<!DOCTYPE html>
<html lang="en">
<head>
<meta charset="utf-8">
<title>Quarrystone Development Group, LLC — Business Card</title>
<link rel="stylesheet" href="https://fonts.googleapis.com/css2?family=Cinzel:wght@400&family=Tinos&display=swap">
<style>
  :root {
    --backdrop: #2b2b2c;
    --front-top: #5d6273;
    --front-bottom: #4a505f;
    --front-ink: #eceef2;
    --back-paper: #f1f1f2;
    --back-paper-edge: #e4e4e6;
    --slate-ink: #444a5b;
    --muted-ink: #55596a;
  }
  * { box-sizing: border-box; margin: 0; padding: 0; }
  html, body { width: 1200px; height: 1138px; overflow: hidden; }
  body { background: var(--backdrop); position: relative; }

  .card {
    position: absolute;
    width: 620px;
    height: 376px;
    border-radius: 16px;
    overflow: hidden;
  }
  .card--front {
    left: 272px; top: 184px;
    background: linear-gradient(180deg, var(--front-top), var(--front-bottom));
  }
  .card--back {
    left: 274px; top: 606px;
    background: linear-gradient(135deg, var(--back-paper), var(--back-paper-edge));
  }

  .wordmark__name {
    font-family: "Cinzel", serif;
    font-weight: 400;
    letter-spacing: 1px;
    line-height: 1;
  }
  .wordmark__tagline {
    font-family: "Cinzel", serif;
    font-weight: 400;
    letter-spacing: 2.4px;
    line-height: 1;
  }

  .card--front .wordmark {
    position: absolute;
    left: 0; right: 0; top: 146px;
    text-align: center;
    color: var(--front-ink);
  }
  .card--front .wordmark__name { font-size: 44px; }
  .card--front .wordmark__tagline { font-size: 18px; margin-top: 14px; }

  .card--back .wordmark {
    position: absolute;
    right: 30px; top: 44px;
    text-align: right;
    color: var(--slate-ink);
  }
  .card--back .wordmark__name { font-size: 36px; }
  .card--back .wordmark__tagline { font-size: 15px; margin-top: 12px; }

  .person {
    position: absolute;
    right: 30px; top: 160px;
    text-align: right;
    color: var(--slate-ink);
  }
  .person__name { font-family: "Cinzel", serif; font-size: 22px; letter-spacing: 0.5px; }
  .person__title { font-family: "Tinos", serif; font-size: 14px; margin-top: 6px; color: var(--muted-ink); }

  .contact {
    position: absolute;
    right: 30px; top: 236px;
    list-style: none;
    text-align: right;
    font-family: "Tinos", serif;
    font-size: 14.5px;
    color: var(--muted-ink);
  }
  .contact li { height: 23px; line-height: 23px; display: flex; justify-content: flex-end; align-items: center; gap: 10px; }
  .contact li.address-line { padding-right: 0; }
  .contact .icon { width: 13px; height: 13px; flex: none; }
</style>
</head>
<body>

  <section class="card card--front" aria-label="Card front">
    <div class="wordmark">
      <div class="wordmark__name">QUARRYSTONE</div>
      <div class="wordmark__tagline">DEVELOPMENT GROUP, LLC</div>
    </div>
  </section>

  <section class="card card--back" aria-label="Card back">
    <div class="wordmark">
      <div class="wordmark__name">QUARRYSTONE</div>
      <div class="wordmark__tagline">DEVELOPMENT GROUP, LLC</div>
    </div>

    <div class="person">
      <div class="person__name">JORDAN ASHBY REEVE</div>
      <div class="person__title">Managing Director</div>
    </div>

    <ul class="contact">
      <li class="address-line">48 Ledger St., Harlow City,</li>
      <li class="address-line">Fairmont, US 204817</li>
      <li>555-014-2200
        <svg class="icon" viewBox="0 0 16 16" aria-hidden="true"><path fill="#55596a" d="M2 6c0-2 2.5-3 6-3s6 1 6 3v1h-3V5.5H5V7H2zM4 8h8l1.5 5h-11z"/></svg>
      </li>
      <li>jordan@quarrystonedev.com
        <svg class="icon" viewBox="0 0 16 16" aria-hidden="true"><rect x="1" y="3" width="14" height="10" fill="#55596a"/><path d="M1.5 3.5L8 9l6.5-5.5" stroke="#f1f1f2" stroke-width="1.2" fill="none"/></svg>
      </li>
      <li>www.quarrystonedev.com
        <svg class="icon" viewBox="0 0 16 16" aria-hidden="true"><g fill="none" stroke="#55596a" stroke-width="1.3"><circle cx="8" cy="8" r="6.3"/><ellipse cx="8" cy="8" rx="2.8" ry="6.3"/><path d="M1.7 8h12.6M2.8 4.8h10.4M2.8 11.2h10.4"/></g></svg>
      </li>
    </ul>
  </section>

</body>
</html>
```